Craft brewery keg badge / badge branding to be on display on keg fonts in pubs and craft beer bars

We're a small craft beer producer and are looking to have a keg badge designed to be put onto keg fonts in bars as well as being used on our bottles. Our website is www.qelnoriales.co.uk. -Please take a look at our site however we're looking for new branding! We're not looking to have the windmill on the badge! We want a bold geometric hop design in the centre of the design. The beer is a low AVB beer (2.9% ABV) and will be hopped with Cascade, Colombus and Tarvel hops and will have a fruity / juicy aroma. We're looking to have a design that we can re-use again and again by changing: colours and wording for different beers in the future.

Target Market(s)
Craft beer drinkers
Industry/Entity Type
Craft Brewery
Requirements
Must have
- Simple, elegant, repeatable core message from the badge. It need a simple, bold geometric hop design (examples uploaded) in the centre which is repeatable across many brands in the future.
- The badge needs to be circular and 82mm across to fit our tap lenses (see http://www.vindex.co.uk/branding for the flat lens). The keg badge needs to be modern and in line with other keg badges like the examples attached- though we leave the artistic flair up to you guys. Please see below the styles of keg badge we like.
- Must be in vector file format and we must get a jpeg version too.

Should not have
- Should not be overcrowded and try to be too full of information. See attached examples.

```html
<!DOCTYPE html>
<html lang="en">
<head>
<meta charset="utf-8">
<title>Craft Brewery Keg Badge</title>
<link rel="stylesheet" href="https://fonts.googleapis.com/css2?family=Germania+One&display=swap">
<style>
  :root {
    --page: #ffffff;
    --badge-fill: #f4a64b;
    --ink: #2b2321;
    --ray: #c8873c;
  }
  html, body {
    margin: 0;
    padding: 0;
    width: 1200px;
    height: 1200px;
    overflow: hidden;
    background: var(--page);
  }
  .keg-badge {
    display: block;
    width: 1200px;
    height: 1200px;
  }
  .badge-type {
    font-family: "Germania One", serif;
    fill: var(--ink);
    stroke: var(--ink);
    stroke-width: 1.5;
  }
  .badge-title { font-size: 100px; letter-spacing: 3px; stroke-width: 3; }
  .badge-since { font-size: 46px; letter-spacing: 3px; }
  .badge-site { font-size: 60px; letter-spacing: 1px; stroke-width: 2; }
  .badge-abv { font-size: 46px; letter-spacing: 3px; }
  .rule { stroke: var(--ink); stroke-width: 3; }
  .rays line {
    stroke: var(--ray);
    stroke-width: 4;
    opacity: 0.75;
  }
</style>
</head>
<body>
<svg class="keg-badge" viewBox="0 0 1200 1200" xmlns="http://www.w3.org/2000/svg">
  <defs>
    <path id="title-arc" d="M 190 335 A 753 753 0 0 1 1010 335"/>
    <radialGradient id="hop-tone" cx="0.5" cy="0.48" r="0.5">
      <stop offset="0" stop-color="#2b2321" stop-opacity="0.75"/>
      <stop offset="0.6" stop-color="#2b2321" stop-opacity="0.4"/>
      <stop offset="1" stop-color="#2b2321" stop-opacity="0"/>
    </radialGradient>
  </defs>

  <circle class="badge-disc" cx="598" cy="593" r="550" fill="var(--badge-fill)" stroke="#000" stroke-width="13"/>

  <g class="rays">
    <line x1="598" y1="250" x2="598" y2="120"/>
    <line x1="770" y1="295" x2="850" y2="140"/>
    <line x1="880" y1="390" x2="1000" y2="300"/>
    <line x1="905" y1="470" x2="1050" y2="410"/>
    <line x1="905" y1="585" x2="1110" y2="585"/>
    <line x1="880" y1="660" x2="1060" y2="755"/>
    <line x1="830" y1="780" x2="970" y2="900"/>
    <line x1="720" y1="860" x2="800" y2="1010"/>
    <line x1="520" y1="860" x2="430" y2="1010"/>
    <line x1="400" y1="790" x2="240" y2="910"/>
    <line x1="330" y1="690" x2="160" y2="755"/>
    <line x1="300" y1="585" x2="100" y2="585"/>
    <line x1="300" y1="470" x2="150" y2="410"/>
    <line x1="330" y1="390" x2="210" y2="300"/>
    <line x1="430" y1="300" x2="360" y2="130"/>
    <line x1="520" y1="260" x2="520" y2="80"/>
  </g>

  <text class="badge-type badge-title" text-anchor="middle">
    <textPath href="#title-arc" startOffset="50%">CRAFT BREWERY</textPath>
  </text>

  <rect class="hop-artwork" role="img" aria-label="Bold geometric line-drawn hop cone with stem, centred on the badge" x="390" y="235" width="420" height="670" fill="url(#hop-tone)"/>

  <g class="since-mark">
    <line class="rule" x1="138" y1="548" x2="298" y2="548"/>
    <text class="badge-type badge-since" x="218" y="595" text-anchor="middle">SINCE</text>
    <line class="rule" x1="138" y1="610" x2="298" y2="610"/>
  </g>
  <g class="year-mark">
    <line class="rule" x1="905" y1="548" x2="1065" y2="548"/>
    <text class="badge-type badge-since" x="985" y="595" text-anchor="middle">1930</text>
    <line class="rule" x1="905" y1="610" x2="1065" y2="610"/>
  </g>

  <text class="badge-type badge-site" x="618" y="1015" text-anchor="middle">QELNORIALES.CO.UK</text>
  <text class="badge-type badge-abv" x="614" y="1100" text-anchor="middle">2.9% ABV</text>
</svg>
</body>
</html>
```